Criação de Layout de site para Computador & Internet
A empresa queria:
" Provedor de Internet banda larga para pessoas físicas e jurídicas com cobertura em duas cidades na região dos lagos, no Rio de Janeiro. "

```html
<!DOCTYPE html>
<html lang="pt-BR">
<head>
<meta charset="UTF-8">
<title>Fibra Óptica – Planos Residenciais</title>
<link rel="stylesheet" href="https://fonts.googleapis.com/css2?family=Montserrat:wght@400;500;600;700;800;900&display=swap">
<style>
:root{
  --bg:#ebebeb;
  --white:#ffffff;
  --orange:#f0771f;
  --orange-deep:#e4610f;
  --orange-light:#f7a04f;
  --orange-soft:#fde6d2;
  --text:#6b6b6b;
}
*{margin:0;padding:0;box-sizing:border-box}
html,body{width:1200px;height:1200px;overflow:hidden;background:var(--bg);font-family:"Montserrat",sans-serif}
.page{position:absolute;left:43px;top:276px;width:1114px;height:648px;background:var(--white);overflow:visible}
.page-glow{position:absolute;inset:80px 0 10px 0;background:radial-gradient(ellipse at 85% 40%,rgba(240,119,31,.08),transparent 60%);}
.top-band{position:absolute;left:0;top:0;width:100%;height:80px;background:linear-gradient(100deg,var(--orange-deep) 0%,var(--orange) 55%,var(--orange-light) 80%,var(--orange) 100%);overflow:hidden}
.top-band__text{position:absolute;left:18px;top:22px;color:var(--white);font-size:12.5px;font-weight:700;line-height:1.45}
.hero-person{position:absolute;left:749px;top:-38px;width:240px;height:118px;border-radius:30px 30px 0 0;background:linear-gradient(160deg,#d9a36e,#c98a4d 50%,#f1a23a)}
.heading{position:absolute;left:0;width:100%;text-align:center}
.heading__title{top:92px;font-size:40px;font-weight:700;color:var(--orange)}
.heading__sub{top:141px;font-size:25px;font-weight:400;color:var(--orange-light)}
.plans{position:absolute;left:197px;top:211px;display:flex;gap:17px}
.plan{width:168px;height:300px;border:3px solid var(--orange);border-radius:24px;background:var(--white);text-align:center;padding-top:12px;color:var(--orange)}
.plan__label{font-size:8px;font-weight:700;color:var(--orange-deep)}
.plan__speed{font-size:46px;font-weight:900;line-height:1;margin-top:2px;letter-spacing:-1px}
.plan__unit{font-size:16px;font-weight:800;line-height:1}
.plan__for{font-size:12px;font-weight:800;line-height:1.05;margin-top:10px}
.plan__price{display:flex;justify-content:center;align-items:flex-start;margin-top:2px}
.plan__cur{font-size:9px;font-weight:700;margin-top:18px;margin-right:3px}
.plan__int{font-size:38px;font-weight:900;line-height:1;letter-spacing:-1px}
.plan__dec{display:flex;flex-direction:column;font-size:10px;font-weight:800;margin-top:5px;line-height:1.2;text-align:left}
.plan__dec small{font-size:7px}
.plan__btn{display:inline-block;margin-top:4px;background:var(--orange);color:var(--white);font-size:8px;font-weight:700;padding:3px 10px;border-radius:10px}
.plan__apps{margin:12px 14px 6px;padding-bottom:6px;border-bottom:1px solid var(--orange-soft);font-size:8px;font-weight:700;text-align:left;color:var(--orange-deep)}
.plan__features{list-style:none;margin:0 14px;text-align:left}
.plan__features li{display:flex;align-items:center;gap:5px;font-size:7.5px;color:var(--text);padding:3px 0;border-bottom:1px solid #f3f3f3}
.plan__features svg{flex:none}
.bottom-line{position:absolute;left:0;top:636px;width:100%;height:6px;background:linear-gradient(90deg,var(--orange-deep),var(--orange-light))}
</style>
</head>
<body>
<div class="page">
  <div class="page-glow"></div>
  <div class="top-band">
    <p class="top-band__text">Internet residencial de qualidade para manter sua família sempre conectada!<br>Escolha o plano ideal e assine agora o melhor provedor da região!</p>
  </div>
  <div class="hero-person" role="img" aria-label="Foto de pessoa usando o celular"></div>

  <h1 class="heading heading__title">Fibra Óptica</h1>
  <h2 class="heading heading__sub">Planos Residenciais</h2>

  <div class="plans">
    <div class="plan">
      <div class="plan__label">Velocidade</div>
      <div class="plan__speed">350</div>
      <div class="plan__unit">MEGAS</div>
      <div class="plan__for">POR<br>APENAS</div>
      <div class="plan__price"><span class="plan__cur">R$</span><span class="plan__int">89</span><span class="plan__dec">,99<small>/MÊS</small></span></div>
      <span class="plan__btn">EU QUERO</span>
      <div class="plan__apps">Apps inclusos</div>
      <ul class="plan__features">
        <li><svg width="8" height="8" viewBox="0 0 8 8"><path d="M1 4l2 2 4-5" fill="none" stroke="#f0771f" stroke-width="1.4"/></svg>Instalação grátis em 24h</li>
        <li><svg width="8" height="8" viewBox="0 0 8 8"><path d="M1 4l2 2 4-5" fill="none" stroke="#f0771f" stroke-width="1.4"/></svg>Velocidade garantida</li>
        <li><svg width="8" height="8" viewBox="0 0 8 8"><path d="M1 4l2 2 4-5" fill="none" stroke="#f0771f" stroke-width="1.4"/></svg>Roteador Wi-Fi incluso</li>
        <li><svg width="8" height="8" viewBox="0 0 8 8"><path d="M1 4l2 2 4-5" fill="none" stroke="#f0771f" stroke-width="1.4"/></svg>Suporte técnico 24 horas</li>
        <li><svg width="8" height="8" viewBox="0 0 8 8"><path d="M1 4l2 2 4-5" fill="none" stroke="#f0771f" stroke-width="1.4"/></svg>Sem taxa de adesão</li>
      </ul>
    </div>
    <div class="plan">
      <div class="plan__label">Velocidade</div>
      <div class="plan__speed">450</div>
      <div class="plan__unit">MEGAS</div>
      <div class="plan__for">POR<br>APENAS</div>
      <div class="plan__price"><span class="plan__cur">R$</span><span class="plan__int">99</span><span class="plan__dec">,99<small>/MÊS</small></span></div>
      <span class="plan__btn">EU QUERO</span>
      <div class="plan__apps">Apps inclusos</div>
      <ul class="plan__features">
        <li><svg width="8" height="8" viewBox="0 0 8 8"><path d="M1 4l2 2 4-5" fill="none" stroke="#f0771f" stroke-width="1.4"/></svg>Instalação grátis em 24h</li>
        <li><svg width="8" height="8" viewBox="0 0 8 8"><path d="M1 4l2 2 4-5" fill="none" stroke="#f0771f" stroke-width="1.4"/></svg>Velocidade garantida</li>
        <li><svg width="8" height="8" viewBox="0 0 8 8"><path d="M1 4l2 2 4-5" fill="none" stroke="#f0771f" stroke-width="1.4"/></svg>Roteador Wi-Fi incluso</li>
        <li><svg width="8" height="8" viewBox="0 0 8 8"><path d="M1 4l2 2 4-5" fill="none" stroke="#f0771f" stroke-width="1.4"/></svg>Suporte técnico 24 horas</li>
        <li><svg width="8" height="8" viewBox="0 0 8 8"><path d="M1 4l2 2 4-5" fill="none" stroke="#f0771f" stroke-width="1.4"/></svg>Sem taxa de adesão</li>
      </ul>
    </div>
    <div class="plan">
      <div class="plan__label">Velocidade</div>
      <div class="plan__speed">500</div>
      <div class="plan__unit">MEGAS</div>
      <div class="plan__for">POR<br>APENAS</div>
      <div class="plan__price"><span class="plan__cur">R$</span><span class="plan__int">109</span><span class="plan__dec">,99<small>/MÊS</small></span></div>
      <span class="plan__btn">EU QUERO</span>
      <div class="plan__apps">Apps inclusos</div>
      <ul class="plan__features">
        <li><svg width="8" height="8" viewBox="0 0 8 8"><path d="M1 4l2 2 4-5" fill="none" stroke="#f0771f" stroke-width="1.4"/></svg>Instalação grátis em 24h</li>
        <li><svg width="8" height="8" viewBox="0 0 8 8"><path d="M1 4l2 2 4-5" fill="none" stroke="#f0771f" stroke-width="1.4"/></svg>Velocidade garantida</li>
        <li><svg width="8" height="8" viewBox="0 0 8 8"><path d="M1 4l2 2 4-5" fill="none" stroke="#f0771f" stroke-width="1.4"/></svg>Roteador Wi-Fi incluso</li>
        <li><svg width="8" height="8" viewBox="0 0 8 8"><path d="M1 4l2 2 4-5" fill="none" stroke="#f0771f" stroke-width="1.4"/></svg>Suporte técnico 24 horas</li>
        <li><svg width="8" height="8" viewBox="0 0 8 8"><path d="M1 4l2 2 4-5" fill="none" stroke="#f0771f" stroke-width="1.4"/></svg>Sem taxa de adesão</li>
      </ul>
    </div>
    <div class="plan">
      <div class="plan__label">Velocidade</div>
      <div class="plan__speed">600</div>
      <div class="plan__unit">MEGAS</div>
      <div class="plan__for">POR<br>APENAS</div>
      <div class="plan__price"><span class="plan__cur">R$</span><span class="plan__int">119</span><span class="plan__dec">,99<small>/MÊS</small></span></div>
      <span class="plan__btn">EU QUERO</span>
      <div class="plan__apps">Apps inclusos</div>
      <ul class="plan__features">
        <li><svg width="8" height="8" viewBox="0 0 8 8"><path d="M1 4l2 2 4-5" fill="none" stroke="#f0771f" stroke-width="1.4"/></svg>Instalação grátis em 24h</li>
        <li><svg width="8" height="8" viewBox="0 0 8 8"><path d="M1 4l2 2 4-5" fill="none" stroke="#f0771f" stroke-width="1.4"/></svg>Velocidade garantida</li>
        <li><svg width="8" height="8" viewBox="0 0 8 8"><path d="M1 4l2 2 4-5" fill="none" stroke="#f0771f" stroke-width="1.4"/></svg>Roteador Wi-Fi incluso</li>
        <li><svg width="8" height="8" viewBox="0 0 8 8"><path d="M1 4l2 2 4-5" fill="none" stroke="#f0771f" stroke-width="1.4"/></svg>Suporte técnico 24 horas</li>
        <li><svg width="8" height="8" viewBox="0 0 8 8"><path d="M1 4l2 2 4-5" fill="none" stroke="#f0771f" stroke-width="1.4"/></svg>Sem taxa de adesão</li>
      </ul>
    </div>
  </div>

  <div class="bottom-line"></div>
</div>
</body>
</html>
```